Using attached logo that has been created

Business card with logo that's attached. Maybe with water or the cartoon van in background. Looking for it to not be so plain and not too white.
Information to include;
Rodney Ashcombe
(555) 218-7730
Info@bramleypipeworks.example
www.bramleypipeworks.example
License # 4627195
Looking forward to the designs u come up with.
Thank you!
-Delphine
Target Market(s)
Plumbing
Industry/Entity Type
Plumbing
Contact Information for Business Card
Listed above

```html
<!DOCTYPE html>
<html lang="en">
<head>
<meta charset="utf-8">
<title>Bramley Pipeworks – Business Card</title>
<link rel="stylesheet" href="https://fonts.googleapis.com/css2?family=Arimo:wght@400;700&display=swap">
<style>
  :root {
    --backdrop: #a9a9a9;
    --brand-blue: #1753a8;
    --brand-yellow: #f2b705;
    --ink: #1d1d1d;
    --card-white: #ffffff;
    --water-light: #5fd3ec;
    --water-mid: #2aa9cf;
    --water-deep: #3d7f9c;
    --figure-blue: #2a62c2;
    --figure-tan: #a98b5e;
  }
  * { box-sizing: border-box; margin: 0; padding: 0; }
  html, body {
    width: 1200px; height: 900px; overflow: hidden;
    background: var(--backdrop);
    font-family: "Arimo", Arial, sans-serif;
  }
  .stage { position: relative; width: 1200px; height: 900px; }
  .card {
    position: absolute; left: 250px; width: 700px; height: 400px;
    border-radius: 34px; overflow: hidden;
    box-shadow: 0 10px 22px rgba(0,0,0,.35);
  }
  .card--front { top: 40px; }
  .card--back { top: 470px; background: var(--card-white); }

  .water-surface {
    position: absolute; inset: 0;
    background: radial-gradient(ellipse at 20% 70%, var(--water-light) 0%, var(--water-mid) 50%, var(--water-deep) 100%);
  }
  .front-figure {
    position: absolute; left: 290px; top: 70px; width: 130px; height: 200px;
    border-radius: 60px 60px 20px 20px;
    background: linear-gradient(180deg, var(--figure-blue) 0%, var(--figure-blue) 50%, var(--figure-tan) 100%);
    opacity: .85;
  }
  .front-brand {
    position: absolute; left: 0; right: 0; top: 285px;
    text-align: center;
  }
  .brand-name {
    font-weight: 700; color: var(--brand-blue);
    text-transform: uppercase; white-space: nowrap;
  }
  .front-brand .brand-name { font-size: 44px; letter-spacing: 1px; }

  .back-info {
    position: absolute; left: 60px; top: 80px; width: 400px;
    z-index: 2;
  }
  .back-info .brand-name { font-size: 32px; letter-spacing: 0; }
  .brand-rule {
    width: 340px; height: 3px; background: var(--brand-blue); margin: 10px 0 26px;
  }
  .holder-name {
    font-size: 28px; font-weight: 400; color: var(--brand-blue);
    text-transform: uppercase; letter-spacing: 1px; margin-bottom: 16px;
    white-space: nowrap;
  }
  .contact-list { list-style: none; }
  .contact-list li {
    display: flex; align-items: center; gap: 10px;
    font-size: 20px; color: var(--ink); line-height: 30px; white-space: nowrap;
  }
  .contact-list svg { width: 20px; height: 20px; flex: none; }
  .license { margin-top: 14px; font-size: 22px; color: var(--brand-blue); }
  .license .license-number { color: var(--brand-yellow); }
  .back-figure {
    position: absolute; right: 10px; top: 20px; width: 200px; height: 380px;
    border-radius: 100px 100px 10px 10px;
    background: linear-gradient(180deg, #d9d9d9 0%, var(--figure-blue) 35%, var(--figure-blue) 60%, var(--figure-tan) 100%);
    opacity: .8;
    z-index: 1;
  }
</style>
</head>
<body>
<main class="stage">
  <section class="card card--front">
    <div class="water-surface" role="img" aria-label="Close-up photograph of water droplets on a blue surface"></div>
    <div class="front-figure" role="img" aria-label="Cartoon plumber mascot holding a pipe wrench and circular saw"></div>
    <div class="front-brand"><span class="brand-name">Bramley Pipeworks</span></div>
  </section>

  <section class="card card--back">
    <div class="back-info">
      <div class="brand-name">Bramley Pipeworks</div>
      <div class="brand-rule"></div>
      <div class="holder-name">Rodney Ashcombe</div>
      <ul class="contact-list">
        <li>
          <svg viewBox="0 0 24 24" aria-hidden="true"><path fill="#1753a8" d="M6.6 10.8a15 15 0 0 0 6.6 6.6l2.2-2.2a1 1 0 0 1 1-.25 11.4 11.4 0 0 0 3.6.57 1 1 0 0 1 1 1V20a1 1 0 0 1-1 1A17 17 0 0 1 3 4a1 1 0 0 1 1-1h3.5a1 1 0 0 1 1 1c0 1.25.2 2.450.57 3.57a1 1 0 0 1-.25 1z"/></svg>
          (555) 218-7730
        </li>
        <li>
          <svg viewBox="0 0 24 24" aria-hidden="true"><rect x="2" y="5" width="20" height="14" rx="1" fill="#1753a8"/><path d="M2 6l10 7 10-7" fill="none" stroke="#fff" stroke-width="1.6"/></svg>
          Info@bramleypipeworks.example
        </li>
        <li>
          <svg viewBox="0 0 24 24" aria-hidden="true"><circle cx="12" cy="12" r="9.5" fill="none" stroke="#1753a8" stroke-width="2"/><ellipse cx="12" cy="12" rx="4" ry="9.5" fill="none" stroke="#1753a8" stroke-width="1.6"/><path d="M3 12h18M4.5 7.5h15M4.5 16.5h15" stroke="#1753a8" stroke-width="1.4"/></svg>
          www.bramleypipeworks.example
        </li>
      </ul>
      <div class="license">License <span class="license-number"># 4627195</span></div>
    </div>
    <div class="back-figure" role="img" aria-label="Cartoon plumber mascot in blue shirt holding a pipe wrench and circular saw"></div>
  </section>
</main>
</body>
</html>
```